New Business Card for Software Company

We are looking at rebranding a 10 year old company that specializes in PDF and DWF solutions for Architects and Engineers. We will attach the new company logo that we are going with so you can work with that and complimentary colors.
The sample information we would like on the business card is:
Gerald Pinfold
Vice President
4738 W. Harrowgate Lane. STE 305
PMB#417
Mesa, AZ 85374
866-392-5074 US Toll Free
123-456-3190 Cell
gpinfold@plavorix.com
The old tag line that we had on the business cars was.
Providing Industrial Strength PDF and DWF Solutions to the Global CAD Marketplace.
If you have an idea for a better tag line we are open to that also.
Updates
We would like to thank all of the Designers for their wonderful work. We apologize that we will not have the time to provide feedback to everyone. There is just so many innovative and professional designs that you have all created making our decision even harder.
Target Market(s)
Architects and Engineers
Industry/Entity Type
Business
Look and feel

```html
<!DOCTYPE html>
<html lang="en">
<head>
<meta charset="utf-8">
<title>Plavorix Business Card</title>
<link rel="stylesheet" href="https://fonts.googleapis.com/css2?family=Arimo:wght@400;700&display=swap">
<style>
  :root {
    --bg: #e6e6ec;
    --card: #ffffff;
    --orange: #e8561f;
    --orange-light: #f59a3c;
    --ink: #3a3a3a;
    --grey: #5c5c5c;
    --rule: #b5b5b5;
  }
  * { box-sizing: border-box; margin: 0; padding: 0; }
  html, body {
    width: 1200px; height: 987px; overflow: hidden;
    background: var(--bg);
    font-family: "Arimo", Arial, sans-serif;
    color: var(--ink);
  }
  .canvas { position: relative; width: 1200px; height: 987px; }
  .card {
    position: absolute;
    width: 700px; height: 400px;
    background: var(--card);
    border-radius: 26px;
    box-shadow: 0 10px 28px rgba(0,0,0,0.12);
  }
  /* back side */
  .card-back { left: 440px; top: 60px; }
  .back-name {
    position: absolute; left: 60px; top: 70px;
    font-size: 150px; font-weight: 700; letter-spacing: -4px;
    color: var(--grey); line-height: 1;
  }
  .tagline {
    position: absolute; left: 60px; right: 60px; top: 265px;
    text-align: center; font-size: 22px; line-height: 1.3; color: var(--grey);
  }
  /* front side */
  .card-front { left: 60px; top: 520px; }
  .brand {
    position: absolute; left: 40px; top: 150px;
    display: flex; align-items: center; gap: 12px;
  }
  .brand-dot {
    width: 46px; height: 46px; border-radius: 50%; background: var(--orange);
  }
  .brand-name {
    font-size: 50px; font-weight: 700; letter-spacing: -1.5px;
    color: var(--orange); line-height: 1;
  }
  .divider {
    position: absolute; left: 330px; top: 50px;
    width: 2px; height: 300px; background: var(--rule);
  }
  .divider::before {
    content: ""; position: absolute; left: -1px; top: 0;
    width: 4px; height: 60px;
    background: linear-gradient(var(--orange), var(--orange-light));
  }
  .contact { position: absolute; left: 355px; top: 52px; }
  .person-name {
    font-size: 30px; font-weight: 700; color: var(--orange); line-height: 1.1;
  }
  .person-title { font-size: 21px; color: var(--grey); margin-bottom: 22px; }
  .line {
    display: flex; align-items: center; gap: 10px;
    font-size: 21px; margin-bottom: 8px; color: var(--ink);
  }
  .line svg { width: 16px; height: 16px; flex: none; }
  .address { margin-top: 22px; font-size: 21px; line-height: 1.25; color: var(--ink); }
</style>
</head>
<body>
<div class="canvas">
  <section class="card card-back">
    <div class="back-name">plavorix</div>
    <p class="tagline">Providing Industrial Strength PDF and DWF Solutions<br>to the Global CAD Marketplace</p>
  </section>

  <section class="card card-front">
    <div class="brand">
      <span class="brand-dot"></span>
      <span class="brand-name">plavorix</span>
    </div>
    <div class="divider"></div>
    <div class="contact">
      <div class="person-name">Gerald Pinfold</div>
      <div class="person-title">Vice President</div>
      <div class="line">
        <svg viewBox="0 0 16 16" aria-hidden="true"><circle cx="8" cy="8" r="7" fill="none" stroke="#e8561f" stroke-width="1.5"/><path d="M5 4.5l1.6 0 .6 2-1 .8a5 5 0 0 0 2.5 2.5l.8-1 2 .6v1.6c-3.5.4-7-3-6.5-6.5z" fill="#e8561f"/></svg>
        <span>866-392-5074(US) TF</span>
      </div>
      <div class="line">
        <svg viewBox="0 0 16 16" aria-hidden="true"><rect x="4" y="1" width="8" height="14" rx="1.5" fill="#e8561f"/><rect x="5.5" y="3" width="5" height="6" fill="#fff"/><circle cx="8" cy="12" r="1" fill="#fff"/></svg>
        <span>123-456-3190</span>
      </div>
      <div class="line">
        <svg viewBox="0 0 16 16" aria-hidden="true"><rect x="1" y="3.5" width="14" height="9" rx="1.5" fill="#e8561f"/><path d="M1.5 4.5l6.5 5 6.5-5" fill="none" stroke="#fff" stroke-width="1.3"/></svg>
        <span>gpinfold@plavorix.com</span>
      </div>
      <div class="address">
        4738 W. Harrowgate Lane<br>
        STE 305<br>
        PMB#417, Mesa, AZ 85374
      </div>
    </div>
  </section>
</div>
</body>
</html>
```